Hardcore nerd needs to stand out in a sea of dull Defence business cards

Wombarra Devices is a new Australian consulting engineering company that turns research and theory into practical systems. No evangelistic fluff, just mathematics and physics into electronic and optical circuits for consumer products, scientific research or Defence applications.

We already have a recognised logo (provided) which is often dark blue/black on a light background but we're open to other combinations. (Us engineers tend to have limited aesthetic imagination :)

Some of our recent products have included:
* Instrumentation for electrical testing,
* Radar jammers,
* GPS antenna design,
* Satellite tracking systems,
* High power lasers

We're open to both single and double-sided designs - happy to be convinced either way.

P.S. Another group is working on the web page, so - alas - our web site is currently of no use for images/ideas...

Target Market(s)

Engineering managers,
Scientists

Contact Information for Business Card

Dr Colin Harte
R&D Engineer

colin@wombarradevices.com.au
0427 563 710

PO Box XXX (to be confirmed)
Kelsby ACT 2917
Australia

Font styles to use
Serif
Sans Serif

Colors

Designer to choose colors to be used in the design.

Requirements
Must have
• My contact details!
• I've had many (great) "bold and plain" designs submitted already, so feel free to be artistically creative :)
• Happy to take advice re fonts/colours/printability etc.
Nice to have
• I'm not sure if "lists" are more at home on a CV than a business card, but representative services include:
• Applied electromagnetics
• RF and high speed electronics
• Signal and image processing
• Electro-optical and laser systems
• Concept-to-prototype design services
• If you're considering double sided cards, then often measuring/alignment grids/rulers feature on the back of similar cards.
• e.g. https://www.veltranoptics.example/newgrouppage9.cfm?objectgroup_id=4183
• https://www.veltranoptics.example/newgrouppage9.cfm?objectgroup_ID=4185
• ..or even a "Smith chart" (google will return lots)
• Generic images to represent a capability might work - googling images associated with keyword for each of these areas might help:
• - "passive radar", "phased array", "fdtd", "vircator"
• RF and high speed electronic design
• - "smith chart", "microstrip circuits", "dimensioned drawing", "electronic schematic"
• - "dft", "iir filter"
• - "optical cavity". "laser energy level diagram"
• Background/watermarked images outlines/wireframes/schematics would probably look OK.
Should not have
• If a list of projects/services is provided, it is important not to make the client feel that this is "all" the company can do. Engineering design is a creative discipline (like graphics :)
• Please, no stock "military" snaps like planes, missiles, etc!

```html
<!DOCTYPE html>
<html lang="en">
<head>
<meta charset="utf-8">
<title>Wombarra Devices – Business Card</title>
<link rel="stylesheet" href="https://fonts.googleapis.com/css2?family=Arimo:wght@700&family=Lato:wght@400;700&display=swap">
<style>
  :root {
    --navy: #001f5c;
    --paper: #ffffff;
    --ink: #1a1a1a;
    --backdrop: #d9d9d9;
    --shadow: rgba(0, 0, 0, 0.35);
  }
  * { margin: 0; padding: 0; box-sizing: border-box; }
  html, body {
    width: 1200px;
    height: 802px;
    overflow: hidden;
    background: var(--backdrop);
  }
  .stage {
    position: relative;
    width: 1200px;
    height: 802px;
  }
  .card {
    position: absolute;
    top: 274px;
    width: 443px;
    height: 264px;
    overflow: hidden;
    box-shadow: 3px 4px 6px var(--shadow);
  }
  .card-front { left: 136px; background: var(--paper); }
  .card-back { left: 624px; background: var(--navy); }

  .brand-decoration {
    position: absolute;
    left: 262px;
    top: 0;
    width: 181px;
    height: 264px;
    background: linear-gradient(160deg, #0a2a6b 0%, var(--navy) 70%);
    border-top-left-radius: 120px 140px;
  }

  .holder-name {
    position: absolute;
    left: 19px;
    top: 30px;
    font-family: "Arimo", Arial, sans-serif;
    font-weight: 700;
    font-size: 15.5px;
    color: var(--navy);
    letter-spacing: 0.2px;
  }
  .holder-role {
    position: absolute;
    left: 19px;
    top: 47px;
    font-family: "Lato", sans-serif;
    font-size: 13px;
    color: var(--ink);
  }
  .postal {
    position: absolute;
    left: 20px;
    top: 144px;
    font-family: "Lato", sans-serif;
    font-size: 13px;
    line-height: 16.5px;
    color: var(--ink);
  }
  .contacts {
    position: absolute;
    left: 20px;
    top: 193px;
    list-style: none;
    font-family: "Lato", sans-serif;
    font-size: 13px;
    line-height: 16px;
    color: var(--ink);
  }
  .contacts li { display: flex; align-items: center; gap: 4px; }
  .contacts svg { width: 10px; height: 10px; flex: none; fill: var(--navy); }

  .brand-lockup {
    position: absolute;
    left: 0;
    top: 0;
    width: 100%;
    height: 100%;
    display: flex;
    align-items: center;
    justify-content: center;
    gap: 12px;
  }
  .brand-dot {
    width: 48px;
    height: 48px;
    border-radius: 50%;
    background: var(--paper);
  }
  .brand-name {
    font-family: "Lato", sans-serif;
    font-weight: 700;
    font-size: 26px;
    line-height: 28px;
    color: var(--paper);
    letter-spacing: 1.5px;
    text-transform: uppercase;
  }
</style>
</head>
<body>
<main class="stage">
  <section class="card card-front" aria-label="Card front">
    <div class="brand-decoration" role="img" aria-label="Large brand symbol decoration in navy"></div>
    <h1 class="holder-name">DR COLIN HARTE</h1>
    <p class="holder-role">R&amp;D Engineer</p>
    <address class="postal">PO Box XXX<br>Kelsby ACT 2917, Australia</address>
    <ul class="contacts">
      <li>
        <svg viewBox="0 0 10 10" aria-hidden="true"><path d="M1 3.5C1 2 2.5 1 5 1s4 1 4 2.5L7.5 4 7 3H3l-.5 1zM2.5 5h5l1 4h-7z"/></svg>
        0427 563 710
      </li>
      <li>
        <svg viewBox="0 0 10 10" aria-hidden="true"><path d="M0.5 2h9v6h-9zM1.2 2.6 5 5.6l3.8-3v.9L5 6.5 1.2 3.5z" fill-rule="evenodd"/></svg>
        colin@wombarradevices.com.au
      </li>
      <li>
        <svg viewBox="0 0 10 10" aria-hidden="true"><circle cx="5" cy="5" r="4.5"/></svg>
        www.wombarradevices.com.au
      </li>
    </ul>
  </section>

  <section class="card card-back" aria-label="Card back">
    <div class="brand-lockup">
      <span class="brand-dot" aria-hidden="true"></span>
      <span class="brand-name">Wombarra Devices</span>
    </div>
  </section>
</main>
</body>
</html>
```